NEW Wordpress Website Design for a Dynamic Long Term Healthcare Company in Hawaii

I would like a new website design for my current company, Marlow Health Collective, which has two different brands - Marlow Homecare and Marlow Senior Living. You can see the current website at www.marlowhealth-example.com. The website should be built using Wordpress Software and the Framewise theme. The website should have a local Hawaii island/tropical feel, but look professional for healthcare. I'm looking for something fresh, and want the designer to select colors, styles, etc.

In the Header, on all pages, I would like a menu that includes Home Care, Senior Living, Rates, and About Us.
Under each of the Header Menu Titles, I would like these drop downs included:
Home Care (drop down pages)- Nurse Aide Care, 24-Hour Home Care, Skilled Nursing, Lifestyle Aide, Hospice at Home, Bathing & Meal Service.
Senior Living (drop down pages) - Long-Term Stay, Short-Term Stay.
Rates (drop down page) - Rates.
About Us (drop down pages) - Our Mission, Ohana Talk, About Dana Marlow.

In the footer, on all pages, you should include the address: 248 Pueo Lane, Suite 310, Honolulu, HI 96817. Phone number: 808-555-0172
The footer should also include buttons for a page called Learn, Caregiver Jobs, and each of the service page links to include: Nurse Aide Care, 24-Hour Home Care, Skilled Nursing, Lifestyle Aide, Hospice at Home, Bathing & Meal Service.
Please don't take the current website and redesign a few aspects. I'm looking for a completely different look and feel.

Target Market(s)

40-80 year olds

Industry/Entity Type

Long Term Healthcare

Coding

Coded - Design and coding required

Requirements
Should not have
• Our existing website as a template. We are looking for a complete redesign. Thank you.

```html
<!DOCTYPE html>
<html lang="en">
<head>
<meta charset="utf-8">
<title>Marlow Health Collective — Homecare &amp; Senior Living</title>
<link href="https://fonts.googleapis.com/css2?family=Lexend:wght@300;400;500;600;700&display=swap" rel="stylesheet">
<style>
:root{
  --red:#d8352c;
  --coral:#d9472b;
  --gold:#c47f12;
  --gold-light:#dca33a;
  --ink:#1e1e1e;
  --text:#3a3a3a;
  --muted:#6b6b6b;
  --cream:#f6f0e9;
  --line:#e2dcd5;
  --white:#ffffff;
}
*{box-sizing:border-box;margin:0;padding:0}
html,body{width:1200px;height:4213px;overflow:hidden;background:var(--white)}
body{font-family:"Lexend",sans-serif;color:var(--text)}
.page{position:relative;width:1200px;height:4213px;overflow:hidden}
.abs{position:absolute}
.btn{position:absolute;display:flex;align-items:center;justify-content:center;border-radius:40px;font-size:14px;font-weight:500;letter-spacing:.3px;text-transform:uppercase}
.btn-red{background:var(--red);color:var(--white)}
.swash{display:block}

/* header */
.site-header{position:absolute;left:0;top:0;width:1200px;height:93px;background:var(--white)}
.brand{position:absolute;font-weight:500;font-size:17px;color:var(--coral);line-height:1.1}
.brand.teal{color:#2f7f7a}
.brand .dot{display:inline-block;width:14px;height:14px;border-radius:50%;background:currentColor;vertical-align:-1px;margin-right:6px}
.nav a{position:absolute;top:31px;font-size:13px;font-weight:600;color:var(--coral);text-decoration:none;letter-spacing:.3px}
.nav-underline{position:absolute;left:513px;top:54px;width:84px;height:3px;background:var(--red)}

/* hero */
.hero{position:absolute;left:0;top:93px;width:1200px;height:640px}
.hero-photo{position:absolute;inset:0;background:linear-gradient(90deg,#f1e9d6 0%,#e5dcb4 30%,#c8c07a 55%,#9fa35a 75%,#c99a4a 100%)}
.hero-fade{position:absolute;inset:0;background:linear-gradient(90deg,rgba(255,250,240,.85) 0%,rgba(255,250,240,.55) 35%,rgba(255,250,240,0) 60%)}
.hero-welcome{position:absolute;left:123px;top:170px;font-size:31px;font-weight:300;color:var(--coral)}
.hero-title{position:absolute;left:123px;top:206px;font-size:44px;font-weight:700;line-height:48px;color:var(--ink)}
.btn-gold{background:var(--gold);color:var(--white)}
.btn-outline-white{background:var(--white);color:var(--coral)}

/* section titles */
.section-title{position:absolute;left:0;width:1200px;text-align:center;font-size:38px;font-weight:500;color:var(--ink)}
.section-swash{position:absolute}

/* about */
.about-lead{position:absolute;left:150px;top:864px;width:900px;text-align:center;font-size:21px;font-weight:300;line-height:28px;color:var(--text)}
.about-photo{position:absolute;left:142px;top:996px;width:452px;height:330px;border-radius:90px 0 90px 0;background:linear-gradient(135deg,#4f7a2e,#8fb14a 50%,#b9b49a)}
.about-copy{position:absolute;left:647px;top:1026px;width:430px;font-size:21px;font-weight:300;line-height:28px;color:var(--text)}
.about-copy p+p{margin-top:27px}

/* home care */
.homecare{position:absolute;left:0;top:1439px;width:1200px;height:598px;background:linear-gradient(100deg,#c47a0c 0%,#d79320 55%,#c9851a 100%)}
.band-title{position:absolute;font-size:36px;font-weight:500}
.homecare .band-title{left:117px;top:126px;color:var(--white)}
.homecare-copy{position:absolute;left:115px;top:220px;width:500px;font-size:22px;font-weight:300;line-height:28px;color:var(--white)}
.homecare-photo{position:absolute;left:657px;top:76px;width:440px;height:440px;border-radius:50%;border:8px solid var(--white);background:linear-gradient(160deg,#7a4a22,#b78c5c 50%,#6f8a57)}

/* senior living */
.senior{position:absolute;left:0;top:2037px;width:1200px;height:608px;background:linear-gradient(180deg,#f7f1ea,#f3ebe1)}
.senior-photo{position:absolute;left:0;top:84px;width:551px;height:449px;border-radius:0 225px 225px 0;background:linear-gradient(135deg,#b48a3a,#d36a3c 45%,#8a6f3c)}
.senior .band-title{left:613px;top:104px;color:var(--ink)}
.senior-sub{position:absolute;left:613px;top:196px;font-size:23px;font-weight:300;color:var(--text)}
.senior-copy{position:absolute;left:613px;top:251px;width:500px;font-size:22px;font-weight:300;line-height:28px;color:var(--text)}

/* blogs */
.blog-card{position:absolute;top:2786px;width:320px;height:418px;border:1px solid var(--line);background:var(--white);box-shadow:0 2px 6px rgba(0,0,0,.06)}
.blog-photo{height:208px}
.blog-body{padding:22px 18px 0}
.blog-card h3{font-size:16px;font-weight:600;line-height:24px;color:var(--ink)}
.blog-card p{margin-top:10px;font-size:12px;font-weight:300;line-height:17px;color:var(--text)}
.btn-outline-red{position:absolute;left:20px;bottom:32px;width:128px;height:36px;border:2px solid var(--red);border-radius:20px;display:flex;align-items:center;justify-content:center;font-size:10px;font-weight:500;color:var(--red);text-transform:uppercase}

/* contact */
.contact{position:absolute;left:0;top:3280px;width:1200px;height:598px}
.contact-eyebrow{position:absolute;left:0;top:80px;width:1200px;text-align:center;font-size:17px;font-weight:300;color:#ffe8d6;letter-spacing:.5px}
.contact-title{position:absolute;left:0;top:108px;width:1200px;text-align:center;font-size:36px;font-weight:500;color:var(--white)}
.field{position:absolute;background:var(--white);border-radius:30px;font-size:14px;font-weight:300;color:var(--muted);padding-left:22px;display:flex;align-items:center}
.field.area{border-radius:18px;align-items:flex-start;padding-top:22px}
.btn-send{position:absolute;left:525px;top:464px;width:185px;height:48px;border:2px solid var(--white);border-radius:30px;display:flex;align-items:center;justify-content:center;font-size:14px;color:var(--white);font-weight:500}

/* footer */
.site-footer{position:absolute;left:0;top:3878px;width:1200px;height:335px;background:var(--white)}
.footer-col{position:absolute;top:64px}
.footer-col h4{font-size:14px;font-weight:600;color:var(--ink);letter-spacing:.3px}
.footer-col ul{list-style:none;margin-top:16px}
.footer-col li{font-size:11px;font-weight:300;color:var(--text);line-height:20px}
.contact-line{display:flex;gap:14px;align-items:flex-start;font-size:10px;font-weight:300;line-height:17px;color:var(--text);margin-top:16px}
.social{display:flex;gap:8px;margin-top:18px}
.social span{width:24px;height:24px;border-radius:50%;border:1.5px solid var(--ink)}
.pill{display:flex;align-items:center;justify-content:center;width:123px;height:26px;border-radius:14px;font-size:9px;color:var(--white);text-transform:uppercase;font-weight:500}
.footer-rule{position:absolute;left:0;top:275px;width:1200px;height:1px;background:var(--line)}
.copyright{position:absolute;left:0;top:292px;width:1200px;text-align:center;font-size:10px;color:var(--muted);font-weight:300}
</style>
</head>
<body>
<div class="page">

  <!-- header -->
  <header class="site-header">
    <div class="brand" style="left:133px;top:30px"><span class="dot"></span>Marlow<br>Homecare</div>
    <div class="brand teal" style="left:232px;top:30px"><span class="dot"></span>Marlow<br>Senior Living</div>
    <nav class="nav">
      <a style="left:513px">HOME CARE ▾</a>
      <a style="left:664px">SENIOR LIVING ▾</a>
      <a style="left:840px">RATES ▾</a>
      <a style="left:956px">ABOUT US ▾</a>
    </nav>
    <div class="nav-underline"></div>
  </header>

  <!-- hero -->
  <section class="hero">
    <div class="hero-photo" role="img" aria-label="Three smiling women knitting together on a sofa in a bright living room"></div>
    <div class="hero-fade"></div>
    <div class="hero-welcome">Welcome to Marlow Care</div>
    <h1 class="hero-title">Hawaii’s Choice<br>Homecare &amp;<br>Senior Car</h1>
    <div class="btn btn-gold" style="left:123px;top:378px;width:182px;height:46px">Get in touch</div>
    <div class="btn btn-outline-white" style="left:312px;top:378px;width:182px;height:46px">Learn more</div>
    <svg class="abs" style="left:1128px;top:225px" width="16" height="90" viewBox="0 0 16 90">
      <circle cx="8" cy="5" r="4.5" fill="#fff"/><circle cx="8" cy="30" r="4.5" fill="#fff"/>
      <circle cx="8" cy="55" r="4.5" fill="#fff"/><circle cx="8" cy="80" r="4.5" fill="none" stroke="#fff"/>
    </svg>
    <svg class="abs" style="left:560px;top:522px" width="80" height="16" viewBox="0 0 80 16">
      <circle cx="8" cy="8" r="6" fill="#fff"/><path d="M9.5 5 6.5 8l3 3" stroke="#555" stroke-width="1.5" fill="none"/>
      <circle cx="24" cy="8" r="3" fill="#fff"/><circle cx="33" cy="8" r="3" fill="#ddd"/>
      <circle cx="42" cy="8" r="3" fill="#ddd"/><circle cx="51" cy="8" r="3" fill="#ddd"/>
      <circle cx="69" cy="8" r="6" fill="#fff"/><path d="M67.5 5l3 3-3 3" stroke="#555" stroke-width="1.5" fill="none"/>
    </svg>
    <svg class="abs" style="left:0;top:540px" width="1200" height="100" viewBox="0 0 1200 100" preserveAspectRatio="none">
      <path d="M0 100 L0 95 Q600 -5 1200 85 L1200 100 Z" fill="#fff"/>
    </svg>
    <div class="abs" style="left:599px;top:552px;width:2px;height:90px;background:var(--red)"></div>
  </section>

  <!-- about -->
  <section>
    <h2 class="section-title" style="top:786px">About Marlow Care</h2>
    <svg class="section-swash" style="left:574px;top:838px" width="52" height="12" viewBox="0 0 52 12"><path d="M2 9 Q14 1 26 6 T50 4" stroke="var(--gold)" stroke-width="4" fill="none" stroke-linecap="round"/></svg>
    <p class="about-lead">Marlow Senior Living creates a warm, supportive, and enriching care home environment where seniors can thrive in their golden years. We provide residential care that promotes well-being, connection, and dignity of each individual.</p>
    <svg class="abs" style="left:106px;top:1244px" width="130" height="130" viewBox="0 0 130 130" fill="#bbb">
      <g id="dotcol"><circle cx="4" cy="4" r="2"/><circle cx="4" cy="18" r="2"/><circle cx="4" cy="32" r="2"/><circle cx="4" cy="46" r="2"/><circle cx="4" cy="60" r="2"/><circle cx="4" cy="74" r="2"/><circle cx="4" cy="88" r="2"/><circle cx="4" cy="102" r="2"/><circle cx="4" cy="116" r="2"/></g>
      <circle cx="18" cy="102" r="2"/><circle cx="32" cy="102" r="2"/><circle cx="46" cy="102" r="2"/><circle cx="60" cy="102" r="2"/><circle cx="74" cy="102" r="2"/><circle cx="88" cy="102" r="2"/><circle cx="102" cy="102" r="2"/><circle cx="116" cy="102" r="2"/>
      <circle cx="18" cy="116" r="2"/><circle cx="32" cy="116" r="2"/><circle cx="46" cy="116" r="2"/><circle cx="60" cy="116" r="2"/><circle cx="74" cy="116" r="2"/><circle cx="88" cy="116" r="2"/><circle cx="102" cy="116" r="2"/><circle cx="116" cy="116" r="2"/>
      <circle cx="18" cy="4" r="2"/><circle cx="18" cy="18" r="2"/><circle cx="18" cy="32" r="2"/><circle cx="18" cy="46" r="2"/><circle cx="18" cy="60" r="2"/><circle cx="18" cy="74" r="2"/><circle cx="18" cy="88" r="2"/>
    </svg>
    <div class="about-photo" role="img" aria-label="Caregiver walking alongside a woman using a walker on a tropical garden path"></div>
    <div class="about-copy">
      <p>Marlow Homecare provides a variety of professional in-home health care services throughout the entire island of Oahu.</p>
      <p>Marlow Senior Living, a beautiful Adult Residential Care Home, is located on the windward side of Oahu in Kailua.</p>
    </div>
    <div class="btn btn-red" style="left:639px;top:1261px;width:190px;height:46px">Learn more</div>
  </section>

  <!-- home care -->
  <section class="homecare">
    <h2 class="band-title">Home Care</h2>
    <svg class="abs" style="left:116px;top:172px" width="54" height="12" viewBox="0 0 52 12"><path d="M2 9 Q14 1 26 6 T50 4" stroke="#fff" stroke-width="4" fill="none" stroke-linecap="round"/></svg>
    <p class="homecare-copy">Marlow Homecare understands that every person's care journey is unique. We tailor our in-home services to meet the diverse nurturing experience of professional quality care and safety within the comfort and convenience of your own home.</p>
    <div class="btn btn-red" style="left:113px;top:423px;width:189px;height:46px">Learn more</div>
    <div class="homecare-photo" role="img" aria-label="Caregiver serving a meal to an older couple at a kitchen table"></div>
  </section>

  <!-- senior living -->
  <section class="senior">
    <div class="senior-photo" role="img" aria-label="Fitness instructor leading seniors in a light dumbbell exercise in a living room"></div>
    <h2 class="band-title">Senior Living</h2>
    <svg class="abs" style="left:612px;top:150px" width="54" height="12" viewBox="0 0 52 12"><path d="M2 9 Q14 1 26 6 T50 4" stroke="var(--gold)" stroke-width="4" fill="none" stroke-linecap="round"/></svg>
    <div class="senior-sub">Trusted Care In Our Home</div>
    <p class="senior-copy">Marlow Senior Living creates a warm, supportive, and enriching care home environment where seniors can thrive in their golden years. We provide residential care that promotes well-being, connection, and dignity of each individual.</p>
    <div class="btn btn-red" style="left:611px;top:425px;width:190px;height:46px">Learn more</div>
  </section>

  <!-- blogs -->
  <section>
    <h2 class="section-title" style="top:2697px">Our Latest Blogs</h2>
    <svg class="section-swash" style="left:566px;top:2746px" width="52" height="12" viewBox="0 0 52 12"><path d="M2 9 Q14 1 26 6 T50 4" stroke="var(--gold)" stroke-width="4" fill="none" stroke-linecap="round"/></svg>

    <article class="blog-card" style="left:95px">
      <div class="blog-photo" role="img" aria-label="Portrait of a smiling woman" style="background:linear-gradient(135deg,#d8d8d8,#a8836a)"></div>
      <div class="blog-body">
        <h3>Lorem ipsum dolor sit amet, consectetur adipiscing</h3>
        <p>Sed ut perspiciatis unde omnis iste natus error sit voluptatem accusantium doloremque laudantium, totam rem aperiam, eaque ipsa</p>
      </div>
      <div class="btn-outline-red">Learn more</div>
    </article>
    <article class="blog-card" style="left:437px">
      <div class="blog-photo" role="img" aria-label="Young caregiver embracing an elderly woman" style="background:linear-gradient(135deg,#eeeeee,#d8c7a8)"></div>
      <div class="blog-body">
        <h3>Lorem ipsum dolor sit amet, consectetur adipiscing</h3>
        <p>Sed ut perspiciatis unde omnis iste natus error sit voluptatem accusantium doloremque laudantium, totam rem aperiam, eaque ipsa</p>
      </div>
      <div class="btn-outline-red">Learn more</div>
    </article>
    <article class="blog-card" style="left:778px">
      <div class="blog-photo" role="img" aria-label="Nurse helping an older man walk with a walker" style="background:linear-gradient(135deg,#cfd6da,#7fa7c2)"></div>
      <div class="blog-body">
        <h3>Lorem ipsum dolor sit amet, consectetur adipiscing</h3>
        <p>Sed ut perspiciatis unde omnis iste natus error sit voluptatem accusantium doloremque laudantium, totam rem aperiam, eaque ipsa</p>
      </div>
      <div class="btn-outline-red">Learn more</div>
    </article>
  </section>

  <!-- contact -->
  <section class="contact">
    <svg class="abs" style="left:0;top:0" width="1200" height="598" viewBox="0 0 1200 598" preserveAspectRatio="none">
      <defs>
        <linearGradient id="contactGrad" x1="0" y1="0" x2="1" y2="1">
          <stop offset="0" stop-color="#e0901e"/><stop offset=".55" stop-color="#e0602a"/><stop offset="1" stop-color="#d72d2e"/>
        </linearGradient>
      </defs>
      <path d="M0 40 Q600 -20 1200 40 L1200 598 L0 598 Z" fill="url(#contactGrad)"/>
    </svg>
    <div class="contact-eyebrow">GET I N TOUCH</div>
    <h2 class="contact-title">Leave us a Message</h2>
    <svg class="abs" style="left:586px;top:157px" width="52" height="12" viewBox="0 0 52 12"><path d="M2 9 Q14 1 26 6 T50 4" stroke="#fff" stroke-width="4" fill="none" stroke-linecap="round"/></svg>
    <div class="field" style="left:209px;top:183px;width:396px;height:54px">Name*</div>
    <div class="field" style="left:616px;top:183px;width:396px;height:54px">Email address*</div>
    <div class="field" style="left:212px;top:251px;width:396px;height:54px">Phone*</div>
    <div class="field" style="left:619px;top:251px;width:396px;height:54px">Company Name*</div>
    <div class="field area" style="left:214px;top:324px;width:795px;height:119px">Type Message</div>
    <div class="btn-send">SEND MESSAGE</div>
  </section>

  <!-- footer -->
  <footer class="site-footer">
    <div class="brand" style="left:176px;top:50px;font-size:16px;color:var(--ink)"><span class="dot"></span>Marlow<br>Health Collective</div>
    <div class="brand" style="left:126px;top:150px;font-size:14px"><span class="dot"></span>Marlow<br>Homecare</div>
    <div class="brand teal" style="left:218px;top:150px;font-size:14px"><span class="dot"></span>Marlow<br>Senior Living</div>

    <div class="footer-col" style="left:363px">
      <h4>COMPANY</h4>
      <svg class="swash" width="30" height="8" viewBox="0 0 52 12"><path d="M2 9 Q14 1 26 6 T50 4" stroke="var(--gold)" stroke-width="5" fill="none"/></svg>
      <ul style="margin-top:6px"><li>Home Care</li><li>Senior Living</li><li>Rates</li><li>About Us</li></ul>
    </div>
    <div class="footer-col" style="left:531px">
      <h4>SERVICES</h4>
      <svg class="swash" width="30" height="8" viewBox="0 0 52 12"><path d="M2 9 Q14 1 26 6 T50 4" stroke="var(--gold)" stroke-width="5" fill="none"/></svg>
      <ul style="margin-top:6px"><li>Nurse Aide Care</li><li>24-Hour Home Care</li><li>Skilled Nursing</li><li>Lifestyle Aide</li><li>Hospice at Home</li><li>Bathing &amp; Meal Service</li></ul>
    </div>
    <div class="footer-col" style="left:719px;width:200px">
      <h4>CONTACT US</h4>
      <svg class="swash" width="30" height="8" viewBox="0 0 52 12"><path d="M2 9 Q14 1 26 6 T50 4" stroke="var(--gold)" stroke-width="5" fill="none"/></svg>
      <div class="contact-line">
        <svg width="16" height="20" viewBox="0 0 16 20"><path d="M8 1a6 6 0 0 0-6 6c0 5 6 12 6 12s6-7 6-12a6 6 0 0 0-6-6z" fill="var(--gold)"/><circle cx="8" cy="7" r="2.3" fill="#fff"/></svg>
        <span>248 Pueo Lane, Suite 310,<br>Honolulu, HI 96817</span>
      </div>
      <div class="contact-line">
        <svg width="16" height="18" viewBox="0 0 24 24"><path d="M6.6 10.8a15 15 0 0 0 6.6 6.6l2.2-2.2a1 1 0 0 1 1-.25 11.4 11.4 0 0 0 3.6.57 1 1 0 0 1 1 1V20a1 1 0 0 1-1 1A17 17 0 0 1 3 4a1 1 0 0 1 1-1h3.5a1 1 0 0 1 1 1c0 1.25.2 2.45.57 3.57a1 1 0 0 1-.25 1z" fill="var(--gold)"/></svg>
        <span>Phone number:<br>808-555-0172</span>
      </div>
    </div>
    <div class="footer-col" style="left:951px">
      <h4>FOLLOW US</h4>
      <svg class="swash" width="30" height="8" viewBox="0 0 52 12"><path d="M2 9 Q14 1 26 6 T50 4" stroke="var(--gold)" stroke-width="5" fill="none"/></svg>
      <div class="social" style="margin-top:10px"><span></span><span></span><span></span><span></span></div>
      <div class="pill" style="background:#e0891c;margin-top:24px;margin-left:-3px">Caregiver jobs</div>
      <div class="pill" style="background:var(--red);margin-top:10px;margin-left:-3px">Learn</div>
    </div>

    <div class="footer-rule"></div>
    <div class="copyright">© 2024 Company Name | All Rights Reserved</div>
  </footer>

</div>
</body>
</html>
```